Korvile

I'd like new business card design options. I'll need to provide updated contact info although after the deign is complete. We are in IT, specifically in the data backup, archiving and disaster recovery verticals.

Industry/Entity Type

Business

```html
<!DOCTYPE html>
<html lang="en">
<head>
<meta charset="utf-8">
<title>Korvile Business Card</title>
<link rel="stylesheet" href="https://fonts.googleapis.com/css2?family=Arimo:wght@400;700&family=Carlito&family=Nunito+Sans:wght@700;800&display=swap">
<style>
  :root {
    --backdrop: #222222;
    --card-white: #ffffff;
    --sky: #0095da;
    --deep-blue: #0059ae;
    --brand-blue: #1a5db3;
    --name-blue: #1f4fa8;
    --ink: #1a1a1a;
    --rule: #9bb8dc;
    --mark-light: #5cb8ea;
  }
  * { margin: 0; padding: 0; box-sizing: border-box; }
  html, body { width: 1200px; height: 900px; overflow: hidden; background: var(--backdrop); }
  .stage { position: relative; width: 1200px; height: 900px; }
  .card {
    position: absolute; top: 306px; width: 440px; height: 271px;
    border-radius: 12px; overflow: hidden;
    box-shadow: 3px 4px 6px rgba(0,0,0,0.45);
  }
  .card-front { left: 149px; background: var(--card-white); }
  .card-back { left: 608px; background: var(--sky); }

  .brand { position: absolute; display: flex; align-items: center; }
  .brand-dot { border-radius: 50%; flex: none; }
  .brand-name { font-family: "Arimo", Arial, sans-serif; font-weight: 700; letter-spacing: 0.14em; }

  .card-front .brand { left: 30px; top: 110px; }
  .card-front .brand-dot { width: 34px; height: 34px; background: var(--brand-blue); margin-right: 12px; }
  .card-front .brand-name { font-size: 22px; color: var(--brand-blue); }

  .divider { position: absolute; left: 238px; top: 68px; width: 1px; height: 134px; background: var(--rule); }

  .contact { position: absolute; left: 256px; top: 62px; font-family: "Carlito", Calibri, sans-serif; color: var(--ink); }
  .person-name { font-family: "Arimo", Arial, sans-serif; font-size: 17px; font-weight: 400; color: var(--name-blue); line-height: 20px; }
  .person-title { font-size: 13px; line-height: 15px; margin-bottom: 7px; }
  .contact-list { list-style: none; }
  .contact-list li { display: flex; align-items: center; font-size: 13px; line-height: 16.3px; }
  .contact-list svg { width: 9px; height: 9px; margin-right: 6px; fill: var(--name-blue); flex: none; }
  .address { font-size: 13px; line-height: 16px; margin-top: 9px; }

  .card-back .brand { left: 96px; top: 96px; }
  .card-back .brand-dot { width: 46px; height: 46px; background: var(--mark-light); margin-right: 12px; }
  .card-back .brand-name { font-size: 27px; color: var(--card-white); }

  .services-band {
    position: absolute; left: 0; bottom: 0; width: 100%; height: 68px;
    background: var(--deep-blue);
    display: flex; align-items: center; justify-content: center;
    font-family: "Nunito Sans", sans-serif; font-weight: 700; font-size: 13px; color: var(--card-white);
    padding-bottom: 4px;
  }
</style>
</head>
<body>
<main class="stage">
  <section class="card card-front">
    <div class="brand">
      <span class="brand-dot"></span>
      <span class="brand-name">KORVILE</span>
    </div>
    <div class="divider"></div>
    <div class="contact">
      <h1 class="person-name">DANIEL CARTER</h1>
      <p class="person-title">Managing Director</p>
      <ul class="contact-list">
        <li><svg viewBox="0 0 10 10"><path d="M0 4 Q5 0 10 4 L8 5 L7 3.5 L3 3.5 L2 5 Z M2 6 L8 6 L9 10 L1 10 Z"/></svg>(044)123456789</li>
        <li><svg viewBox="0 0 10 10"><rect x="0" y="3" width="10" height="7" rx="1"/><rect x="2" y="0" width="5" height="4" fill="#fff" stroke="#1f4fa8"/></svg>(044)123456789</li>
        <li><svg viewBox="0 0 10 10"><rect x="0" y="2" width="10" height="7"/><path d="M0 2 L5 6 L10 2" fill="none" stroke="#fff" stroke-width="1"/></svg>info@youremail.com</li>
        <li><svg viewBox="0 0 10 10"><circle cx="5" cy="5" r="5"/><path d="M3 2 Q5 4 3 7 M6 3 Q8 5 7 8" stroke="#fff" fill="none"/></svg>www.websitename.com</li>
      </ul>
      <p class="address">1234, Address GoesHere,<br>Country name, 12345</p>
    </div>
  </section>

  <section class="card card-back">
    <div class="brand">
      <span class="brand-dot"></span>
      <span class="brand-name">KORVILE</span>
    </div>
    <p class="services-band">Data Backup &nbsp;| Archiving | Disaster Recovery Verticals</p>
  </section>
</main>
</body>
</html>
```